Redesign of the UI of a customer service platform

To improve the user experience of our customers, we need a new design for our agent interface of our customer service platform (velorant.com).
The focus will be on the dashboard and the inbox screens (see attached) along with the common UI elements (Buttons, menu, fonts, forms...)
We want a simple and distinctive design

Target Market(s)

Worldwide

Industry/Entity Type

It Service

Number of Pages Required

3 page

Font styles to use
Sans Serif

Requirements
Must have
• New Onboarding page: this is a new page that is shown to user the first time they login to the platform. This will replace the current onboarding screen (setup SMS, Setup widget...etc)
• Dashboard page: to access important information and activate services (see screenshot from current site)
• Inbox page: to manage all the interactions with customers. (see screenshot from current site)
• UI elements (buttons, menus, forms, tables, fonts, color palette)

```html
<!DOCTYPE html>
<html lang="en">
<head>
<meta charset="utf-8">
<title>brindlo — Dashboard</title>
<link href="https://fonts.googleapis.com/css2?family=Roboto:wght@300;400;500&display=swap" rel="stylesheet">
<style>
:root{
  --orange:#f2511f;
  --sidebar:#3b3b3b;
  --sidebar-line:#474747;
  --page:#e7e8e6;
  --white:#ffffff;
  --ink:#333333;
  --muted:#777777;
  --faint:#9a9a9a;
  --line:#e4e4e4;
  --green:#43a348;
  --teal:#45bfd3;
  --grey-disc:#c4c4c4;
  --row:#f6f6f6;
}
*{box-sizing:border-box;margin:0;padding:0}
html,body{width:1200px;height:712px;overflow:hidden}
body{font-family:"Roboto",Arial,sans-serif;background:var(--page);color:var(--ink);position:relative}

.topbar{position:absolute;left:0;top:0;width:1200px;height:56px;background:var(--white);box-shadow:0 1px 3px rgba(0,0,0,.15);z-index:2}
.brand{position:absolute;left:11px;top:16px;display:flex;align-items:center;gap:6px;font-size:20px;font-weight:500;color:#3a3a3a}
.brand-dot{width:18px;height:18px;border-radius:50%;background:#3a3a3a}
.menu-toggle{position:absolute;left:158px;top:20px;width:21px;height:15px}
.page-title{position:absolute;left:202px;top:18px;font-size:18px;color:#333}
.top-action{position:absolute;top:16px;width:24px;height:24px}
.top-badge{position:absolute;top:-8px;left:10px;min-width:15px;height:15px;border-radius:50%;background:var(--orange);color:#fff;font-size:10px;text-align:center;line-height:15px}

.sidebar{position:absolute;left:0;top:56px;width:136px;height:656px;background:var(--sidebar)}
.nav-item{position:relative;height:90px;border-bottom:1px solid var(--sidebar-line);display:flex;flex-direction:column;align-items:center;justify-content:center;gap:6px;color:#fff;font-size:14px}
.nav-item svg{width:28px;height:28px}
.nav-item.active{background:var(--orange)}
.nav-item.active::after{content:"";position:absolute;right:-9px;top:36px;border-left:9px solid var(--orange);border-top:9px solid transparent;border-bottom:9px solid transparent}

.stats{position:absolute;left:154px;top:77px;width:1028px;height:124px;background:var(--white);display:flex}
.stat{flex:1;display:flex;align-items:flex-start;padding:24px 0 0 29px;gap:16px;border-right:1px solid var(--line)}
.stat:last-child{border-right:0}
.stat-icon{width:54px;height:54px;border-radius:50%;background:var(--orange);display:flex;align-items:center;justify-content:center;margin-top:2px}
.stat-icon svg{width:26px;height:26px}
.stat-value{font-size:26px;font-weight:300;color:#333;line-height:1;margin-top:-1px}
.stat-text{font-size:13.5px;color:var(--muted);line-height:19px;margin-top:8px;width:120px}

.panel{position:absolute;background:var(--white)}
.panel-head{height:48px;border-bottom:1px solid var(--line);display:flex;align-items:center;padding-left:16px;font-size:17px;color:#333;background:#f8f8f8}

.reports{left:153px;top:216px;width:445px;height:385px}
.report-tabs{position:absolute;right:0;top:0;display:flex;height:48px}
.report-tab{width:44px;height:48px;display:flex;align-items:center;justify-content:center}
.report-tab svg{width:18px;height:18px}
.report-tab.active{background:#fff;border-top:3px solid var(--green)}
.report-title{position:absolute;left:17px;top:68px;font-size:13.5px;color:#555}
.report-sub{position:absolute;left:17px;top:91px;font-size:11.5px;color:var(--faint)}
.chart-switch{position:absolute;left:351px;top:74px;display:flex;border:1px solid #ccc}
.chart-switch span{width:40px;height:26px;display:flex;align-items:center;justify-content:center}
.chart-switch span.on{background:#e8e8e8;border-right:1px solid #ccc}
.chart{position:absolute;left:0;top:137px;width:445px;height:188px;background:linear-gradient(90deg,#f7eeeb 0%,#f3ebea 40%,#eef5f7 100%)}
.chart-axis{position:absolute;left:0;top:332px;width:445px;display:flex;justify-content:space-around;padding:0 6px 0 30px;font-size:9.5px;color:#777}

.plan{left:612px;top:216px;width:570px;height:496px}
.upgrade{position:absolute;right:13px;top:10px;width:73px;height:27px;background:var(--green);color:#fff;font-size:12px;font-weight:500;display:flex;align-items:center;justify-content:center}
.addons{display:flex;height:116px;padding-top:14px}
.addon{flex:1;display:flex;flex-direction:column;align-items:center;border-right:1px solid var(--line);margin:16px 0 0;height:84px}
.addon:last-child{border-right:0}
.addon-disc{position:relative;width:58px;height:58px;border-radius:50%;background:var(--grey-disc);display:flex;align-items:center;justify-content:center;margin-top:-16px}
.addon-disc svg{width:28px;height:28px}
.addon-badge{position:absolute;top:-4px;right:-6px;width:18px;height:18px;border-radius:50%;background:var(--orange);color:#fff;font-size:10.5px;text-align:center;line-height:18px}
.addon-name{font-size:14px;color:#666;margin-top:9px}
.addon-limit{font-size:12.5px;color:var(--faint);margin-top:5px}

.services{position:absolute;left:14px;top:191px;width:542px}
.service{position:relative;height:104px;background:var(--row);margin-bottom:3px}
.service-icon{position:absolute;left:15px;top:22px;width:46px;height:46px;border-radius:50%;border:1px solid #ccc;background:#fff;display:flex;align-items:center;justify-content:center}
.service-icon svg{width:22px;height:22px}
.service-name{position:absolute;left:79px;top:22px;font-size:17px;color:#222}
.service-desc{position:absolute;left:81px;top:51px;width:330px;font-size:11.5px;line-height:19px;color:#999}
.service-state{position:absolute;right:12px;top:27px;width:86px;height:24px;background:var(--green);color:#fff;font-size:11.5px;display:flex;align-items:center;justify-content:center;gap:6px}
</style>
</head>
<body>

<header class="topbar">
  <div class="brand"><span class="brand-dot"></span><span>brindlo</span></div>
  <svg class="menu-toggle" viewBox="0 0 21 15"><rect width="21" height="2" fill="#444"/><rect y="6.5" width="21" height="2" fill="#444"/><rect y="13" width="21" height="2" fill="#444"/></svg>
  <div class="page-title">Dashboard</div>
  <div class="top-action" style="left:1097px">
    <svg viewBox="0 0 24 24" width="24" height="24"><path d="M3 13h5l2 3h4l2-3h5v7H3z" fill="#444"/><path d="M12 4v8M8.5 9l3.5 3.5L15.5 9" stroke="#444" stroke-width="2" fill="none"/></svg>
    <span class="top-badge">1</span>
  </div>
  <div class="top-action" style="left:1152px">
    <svg viewBox="0 0 24 24" width="24" height="24"><path d="M14 2l8 8-12 12-8-8z" fill="#444"/><path d="M11 9l4 4" stroke="#fff" stroke-width="2"/></svg>
  </div>
</header>

<nav class="sidebar">
  <div class="nav-item active">
    <svg viewBox="0 0 28 28"><path d="M3 20a11 11 0 0 1 22 0" stroke="#fff" stroke-width="2.5" fill="none"/><path d="M14 20l5-7" stroke="#fff" stroke-width="2.5"/><circle cx="14" cy="20" r="2.5" fill="#fff"/></svg>Dashboard</div>
  <div class="nav-item">
    <svg viewBox="0 0 28 28"><path d="M3 15h7l2 3h4l2-3h7v9H3z" fill="#fff"/><path d="M14 3v11M9.5 10l4.5 4.5 4.5-4.5" stroke="#fff" stroke-width="2.5" fill="none"/></svg>Inbox</div>
  <div class="nav-item">
    <svg viewBox="0 0 28 28"><path d="M17 2l9 9-15 15-9-9z" fill="#fff"/><path d="M13 10l5 5" stroke="#3b3b3b" stroke-width="2.5"/></svg>Tickets</div>
  <div class="nav-item">
    <svg viewBox="0 0 28 28"><circle cx="14" cy="9" r="4" fill="#fff"/><circle cx="6" cy="11" r="3" fill="#fff"/><circle cx="22" cy="11" r="3" fill="#fff"/><path d="M7 24a7 7 0 0 1 14 0z" fill="#fff"/><path d="M0 23a6 6 0 0 1 7-5v5zM28 23a6 6 0 0 0-7-5v5z" fill="#fff"/></svg>Clients</div>
  <div class="nav-item">
    <svg viewBox="0 0 28 28"><rect x="3" y="18" width="4" height="7" fill="#fff"/><rect x="9" y="15" width="4" height="10" fill="#fff"/><rect x="15" y="17" width="4" height="8" fill="#fff"/><rect x="21" y="13" width="4" height="12" fill="#fff"/><path d="M3 14l7-6 5 4 9-8" stroke="#fff" stroke-width="2.5" fill="none"/><path d="M19 3h6v6z" fill="#fff"/></svg>Reports</div>
  <div class="nav-item">
    <svg viewBox="0 0 28 28"><circle cx="14" cy="14" r="8" fill="none" stroke="#fff" stroke-width="5" stroke-dasharray="3.2 3"/><circle cx="14" cy="14" r="6.5" fill="#fff"/><circle cx="14" cy="14" r="3" fill="#3b3b3b"/></svg>Settings</div>
</nav>

<section class="stats">
  <div class="stat">
    <div class="stat-icon"><svg viewBox="0 0 26 26"><circle cx="13" cy="8" r="5" fill="#fff"/><path d="M5 23a8 8 0 0 1 16 0z" fill="#fff"/></svg></div>
    <div><div class="stat-value">0/0</div><div class="stat-text">Lorem Ipsum is simply dummy text</div></div>
  </div>
  <div class="stat">
    <div class="stat-icon"><svg viewBox="0 0 26 26"><path d="M16 2l8 8-14 14-8-8z" fill="#fff"/><path d="M12 9l5 5" stroke="#f2511f" stroke-width="2.5"/></svg></div>
    <div><div class="stat-value">0/0</div><div class="stat-text">Lorem Ipsum is simply dummy text</div></div>
  </div>
  <div class="stat">
    <div class="stat-icon"><svg viewBox="0 0 26 26"><ellipse cx="11" cy="10" rx="9" ry="7" fill="#fff"/><path d="M5 15l-2 5 6-3z" fill="#fff"/><path d="M20 9a7 6 0 0 1-1 12l3 3-7-2" fill="#fff"/></svg></div>
    <div><div class="stat-value">0/0</div><div class="stat-text">Lorem Ipsum is simply dummy text</div></div>
  </div>
  <div class="stat">
    <div class="stat-icon"><svg viewBox="0 0 26 26"><rect x="6" y="2" width="13" height="22" rx="2" fill="#fff"/><rect x="8" y="5" width="9" height="14" fill="#f2511f"/><rect x="13" y="7" width="9" height="6" fill="#fff"/></svg></div>
    <div><div class="stat-value">0/0</div><div class="stat-text">Lorem Ipsum is simply dummy text</div></div>
  </div>
</section>

<section class="panel reports">
  <div class="panel-head">Reports</div>
  <div class="report-tabs">
    <div class="report-tab"><svg viewBox="0 0 18 18"><rect x="3" y="1" width="10" height="16" rx="1.5" fill="none" stroke="#4a9fe0" stroke-width="1.6"/><rect x="9" y="5" width="7" height="5" fill="#4a9fe0"/></svg></div>
    <div class="report-tab"><svg viewBox="0 0 18 18"><ellipse cx="7.5" cy="7" rx="6.5" ry="5" fill="#e99a24"/><path d="M14 7a5 4.5 0 0 1-1 8l2 2-5-1.5" fill="#e99a24"/></svg></div>
    <div class="report-tab"><svg viewBox="0 0 18 18"><path d="M11 1l6 6-10 10-6-6z" fill="#3f87d6"/><path d="M8 6l4 4" stroke="#fff" stroke-width="1.6"/></svg></div>
    <div class="report-tab active"><svg viewBox="0 0 18 18"><circle cx="9" cy="5.5" r="3.5" fill="#43a348"/><path d="M3 17a6 6 0 0 1 12 0z" fill="#43a348"/></svg></div>
  </div>
  <div class="report-title">Lorem Ipsum is simply dummy text</div>
  <div class="report-sub">Lorem Ipsum is simply dummy text</div>
  <div class="chart-switch">
    <span class="on"><svg width="18" height="14" viewBox="0 0 18 14"><path d="M1 1v12h16" stroke="#666" fill="none"/><path d="M5 12V6M8 12V4M11 12V7M14 12V5" stroke="#666"/></svg></span>
    <span><svg width="18" height="14" viewBox="0 0 18 14"><path d="M1 12l5-5 4 3 7-7" stroke="#999" fill="none"/></svg></span>
  </div>
  <div class="chart">
    <svg width="445" height="188" viewBox="0 0 445 188">
      <g stroke="#e3e3e3" stroke-width="1"><line x1="0" y1="31" x2="445" y2="31"/><line x1="0" y1="83" x2="445" y2="83"/><line x1="0" y1="136" x2="445" y2="136"/></g>
      <g font-family="Roboto, sans-serif" font-size="9.5" fill="#888"><text x="21" y="27">3</text><text x="21" y="82">2</text><text x="21" y="135">1</text><text x="21" y="187">0</text></g>
      <polygon points="8,188 53,169 96,135 148,106 198,65 248,85 288,131 336,109 397,100 445,133 445,188" fill="#bfe1e7" opacity=".55"/>
      <polyline points="8,188 53,169 96,135 148,106 198,65 248,85 288,131 336,109 397,100 445,133" fill="none" stroke="#45bfd3" stroke-width="2"/>
      <g fill="#45bfd3"><circle cx="53" cy="169" r="3.5"/><circle cx="96" cy="135" r="3.5"/><circle cx="148" cy="106" r="3.5"/><circle cx="198" cy="65" r="3.5"/><circle cx="248" cy="85" r="3.5"/><circle cx="288" cy="131" r="3.5"/><circle cx="336" cy="109" r="3.5"/><circle cx="397" cy="100" r="3.5"/></g>
    </svg>
  </div>
  <div class="chart-axis"><span>Jan ,21</span><span>Dec ,21</span><span>Nov ,21</span><span>Jan ,21</span><span>Dec ,21</span><span>Jan ,21</span><span>Jan ,21</span></div>
</section>

<section class="panel plan">
  <div class="panel-head">Plan &amp; Add-ons</div>
  <div class="upgrade">Upgrade</div>
  <div class="addons">
    <div class="addon">
      <div class="addon-disc"><svg viewBox="0 0 28 28"><circle cx="14" cy="9" r="4" fill="#fff"/><circle cx="6" cy="11" r="3" fill="#fff"/><circle cx="22" cy="11" r="3" fill="#fff"/><path d="M7 24a7 7 0 0 1 14 0z" fill="#fff"/><path d="M0 23a6 6 0 0 1 7-5v5zM28 23a6 6 0 0 0-7-5v5z" fill="#fff"/></svg><span class="addon-badge">1</span></div>
      <div class="addon-name">Lorem Ipsum</div><div class="addon-limit">Unlimited</div>
    </div>
    <div class="addon">
      <div class="addon-disc"><svg viewBox="0 0 28 28"><rect x="3" y="18" width="4" height="7" fill="#fff"/><rect x="9" y="15" width="4" height="10" fill="#fff"/><rect x="15" y="17" width="4" height="8" fill="#fff"/><rect x="21" y="13" width="4" height="12" fill="#fff"/><path d="M3 14l7-6 5 4 9-8" stroke="#fff" stroke-width="2.5" fill="none"/><path d="M19 3h6v6z" fill="#fff"/></svg><span class="addon-badge">1</span></div>
      <div class="addon-name">Lorem Ipsum</div><div class="addon-limit">Unlimited</div>
    </div>
    <div class="addon">
      <div class="addon-disc"><svg viewBox="0 0 28 28"><path d="M3 15h7l2 3h4l2-3h7v9H3z" fill="#fff"/><path d="M14 3v11M9.5 10l4.5 4.5 4.5-4.5" stroke="#fff" stroke-width="2.5" fill="none"/></svg><span class="addon-badge">1</span></div>
      <div class="addon-name">Lorem Ipsum</div><div class="addon-limit">Unlimited</div>
    </div>
  </div>

  <div class="services">
    <div class="service">
      <div class="service-icon"><svg viewBox="0 0 22 22"><path d="M5 2l4 4-2 3c1 2 3 4 5 5l3-2 4 4-3 3C9 19 3 13 2 5z" fill="#45bfd3"/></svg></div>
      <div class="service-name">Lorum Ipsum test</div>
      <div class="service-desc">Pellentesque habitant morbi tristique senectus et netus et malesuada fames ac turpis egestas. morbi...</div>
      <div class="service-state"><svg width="12" height="10" viewBox="0 0 12 10"><path d="M1 5l3.5 3.5L11 1" stroke="#fff" stroke-width="2" fill="none"/></svg>Activted</div>
    </div>
    <div class="service">
      <div class="service-icon"><svg viewBox="0 0 22 22"><path d="M11 2a9 8.5 0 1 1-4 16l-4 2 1-4A9 8.5 0 0 1 11 2z" fill="#45bfd3"/><rect x="10" y="7" width="2" height="8" fill="#fff"/></svg></div>
      <div class="service-name">Lorum Ipsum test</div>
      <div class="service-desc">Pellentesque habitant morbi tristique senectus et netus et malesuada fames ac turpis egestas. morbi...</div>
      <div class="service-state"><svg width="12" height="10" viewBox="0 0 12 10"><path d="M1 5l3.5 3.5L11 1" stroke="#fff" stroke-width="2" fill="none"/></svg>Activted</div>
    </div>
    <div class="service">
      <div class="service-icon"><svg viewBox="0 0 22 22"><path d="M2 10L20 3l-4 16-5-5-2 4v-6l9-8-10 7z" fill="#45bfd3"/></svg></div>
      <div class="service-name">Lorum Ipsum test</div>
      <div class="service-desc">Pellentesque habitant morbi tristique senectus et netus et malesuada fames ac turpis egestas. morbi...</div>
      <div class="service-state"><svg width="12" height="10" viewBox="0 0 12 10"><path d="M1 5l3.5 3.5L11 1" stroke="#fff" stroke-width="2" fill="none"/></svg>Activted</div>
    </div>
  </div>
</section>

</body>
</html>
```